Redesign of business card for Cedar Ridge Mechanical

We are looking for a new design for our business cards for Cedar Ridge Mechanical. We are a plumbing & HVAC construction company, operating on the West Coast of Canada and USA. Logo attached.
Industry/Entity Type
Construction - Plumbing & HVAC
Contact Information for Business Card
Name, address, phone numbers, email, website address
Look and feel
Each slider illustrates characteristics of the customer's brand and the style your logo design should communicate.

```html
<!DOCTYPE html>
<html lang="en">
<head>
<meta charset="utf-8">
<title>Cedar Ridge Mechanical – Business Card</title>
<link href="https://fonts.googleapis.com/css2?family=Open+Sans:wght@400;700&display=swap" rel="stylesheet">
<style>
  :root {
    --stage: #232323;
    --card-black: #050505;
    --pattern-dark: #0d0d0d;
    --pattern-light: #2a2a2a;
    --white: #ffffff;
    --grey: #8a8c8e;
    --text: #ffffff;
  }
  * { margin: 0; padding: 0; box-sizing: border-box; }
  html, body {
    width: 1200px; height: 711px; overflow: hidden;
    background: var(--stage);
    font-family: "Open Sans", sans-serif;
  }
  .stage {
    position: relative; width: 1200px; height: 711px;
    display: flex; justify-content: center; align-items: center; gap: 70px;
  }
  .card {
    position: relative; width: 310px; height: 540px;
    border-radius: 30px; overflow: hidden;
    background: var(--card-black);
    box-shadow: 0 14px 30px rgba(0,0,0,.55);
  }
  .card-back .pattern {
    position: absolute; inset: 0;
    background: linear-gradient(160deg, var(--pattern-light) 0%, var(--pattern-dark) 45%, var(--pattern-dark) 100%);
  }
  .front-top { position: absolute; top: 0; left: 0; width: 310px; height: 250px; }
  .brand {
    position: absolute; top: 78px; left: 20px; width: 260px;
    display: flex; align-items: center; justify-content: center; gap: 12px;
  }
  .brand-square { flex: none; width: 40px; height: 40px; background: var(--card-black); }
  .brand-name {
    font-weight: 700; font-size: 20px; line-height: 1.15; letter-spacing: 1px;
    text-transform: uppercase; color: var(--card-black);
  }
  .brand-name span { display: block; }
  .front-info {
    position: absolute; top: 262px; left: 0; width: 310px;
    text-align: center; color: var(--text);
  }
  .person-name { font-weight: 700; font-size: 25px; letter-spacing: 1px; line-height: 1.1; }
  .person-title { font-size: 13px; margin-top: 2px; }
  .icon-row {
    display: flex; align-items: center; justify-content: center; gap: 6px;
    margin-top: 14px;
  }
  .rule { width: 30px; height: 1.5px; background: var(--text); }
  .rule-wide { width: 170px; height: 1.5px; background: var(--text); margin: 10px auto; }
  .icon {
    width: 26px; height: 26px; border-radius: 7px; background: var(--white);
    display: flex; align-items: center; justify-content: center;
  }
  .icon svg { width: 16px; height: 16px; }
  .contact-list { list-style: none; margin-top: 12px; font-size: 14px; line-height: 1.45; }
  .address { font-size: 14px; line-height: 1.45; }
</style>
</head>
<body>
<main class="stage">
  <section class="card card-back">
    <div class="pattern" role="img" aria-label="Repeating brand monogram pattern in glossy black on black"></div>
  </section>

  <section class="card card-front">
    <svg class="front-top" viewBox="0 0 310 250" aria-hidden="true">
      <path d="M0 30 Q0 0 30 0 H310 V40 Q310 240 150 240 Q30 240 0 150 Z" fill="var(--grey)"/>
      <path d="M0 30 Q0 0 30 0 H300 V30 Q300 228 145 228 Q25 228 0 140 Z" fill="var(--white)"/>
    </svg>
    <div class="brand">
      <span class="brand-square"></span>
      <p class="brand-name"><span>Cedar Ridge</span><span>Mechanical</span></p>
    </div>

    <div class="front-info">
      <h1 class="person-name">DANIEL HAYES</h1>
      <p class="person-title">Managing Director</p>

      <div class="icon-row">
        <span class="rule"></span>
        <span class="icon"><svg viewBox="0 0 16 16"><path d="M3 2h3l1 3-2 1a8 8 0 0 0 5 5l1-2 3 1v3c0 1-1 1-1 1C7 14 2 9 2 3c0 0 0-1 1-1z" fill="#000"/></svg></span>
        <span class="icon"><svg viewBox="0 0 16 16"><rect x="4" y="1" width="8" height="14" rx="1.5" fill="#000"/><rect x="5.5" y="3" width="5" height="8" fill="#fff"/></svg></span>
        <span class="icon"><svg viewBox="0 0 16 16"><rect x="1" y="3" width="14" height="10" rx="1" fill="#000"/><path d="M1.5 3.5 8 9l6.5-5.5" stroke="#fff" stroke-width="1.3" fill="none"/></svg></span>
        <span class="icon"><svg viewBox="0 0 16 16"><circle cx="8" cy="8" r="6.5" fill="#000"/><path d="M1.5 8h13M8 1.5c-3 3-3 10 0 13M8 1.5c3 3 3 10 0 13" stroke="#fff" stroke-width="1" fill="none"/></svg></span>
        <span class="rule"></span>
      </div>

      <ul class="contact-list">
        <li>555-014-2288</li>
        <li>555-018-3377</li>
        <li>info@cedarridgemech.com</li>
        <li>www.cedarridgemech.com</li>
      </ul>
      <div class="rule-wide"></div>
      <p class="address">4820 Harbor View Rd Suite<br>210 Portland, Oregon 97201</p>
    </div>
  </section>
</main>
</body>
</html>
```